Call Center In Need of Website Design

We are a call center that provides inbound and outbound calling & marketing services for eCommerce store. We would like to see a fun, creative, playful design that is simple.

Here are some sample design sites we like;
- https://www.velmoreline.com/
- https://pindrask.io/
- https://www.glimbertic.com/live-chat-software/
- https://www.zavrolin.com/

Here are some competitor sites;
- https://www.ostrevaglinks.com/
- https://www.helpkestrel.com/

I have attached website content for your use.

Target Market(s)

eCommerce

Coding

Coded - Design and coding required

Number of Pages Required

5+ page

Font styles to use
Sans Serif

Colors

Designer to choose colors to be used in the design.

Requirements
Must have
• Must have designs for the following 5 separate pages;
• 1. Home (landing)
• - This will be were the design style really needs to show.
• - Just needs to touch on key services
• - CTA
• 2. About Us
• - Basic page for about me paragraph
• 3. Services
• - List of services with icons
• - Click on service type to expand details or hover over service icon to view popup bubble with details about that service
• 4. Pricing
• - Option to bundle 1(one) digital service plan and 1(one) call center service plan
• - Bundling adds 10% monthly discount to over all price
• - Customer does NOT have to bundle
• - FAQ
• 5. Contact Us
• - Include a capture form (name, company name, email, phone, message)
• - Contact info
• - Business hours
• When customer purchases their desired plan, then they are taken to a page where they must schedule a call with an account rep.
Nice to have
• home page animations
Should not have
• All information on Home/Landing page.

```html
<!DOCTYPE html>
<html lang="en">
<head>
<meta charset="utf-8">
<title>Lunaro – Omnichannel Customer Care</title>
<link rel="stylesheet" href="https://fonts.googleapis.com/css2?family=Didact+Gothic&family=Montserrat:wght@500;600;700&display=swap">
<style>
  :root{
    --navy-deep:#07111f;
    --navy:#0f2440;
    --teal:#5fc7ad;
    --teal-soft:#6ccab5;
    --teal-card:#84dac4;
    --ink:#1b1d22;
    --muted:#6b7078;
    --grey-bg:#f5f6f7;
    --faq-bg:#eef3f7;
    --white:#ffffff;
    --blue-panel:#23497a;
    --green-panel:#2c7a70;
    --ghost:#e3e5e8;
  }
  *{box-sizing:border-box;margin:0;padding:0}
  html,body{width:1200px;height:2350px;overflow:hidden;background:var(--white)}
  body{font-family:"Didact Gothic",sans-serif;color:var(--ink)}
  .canvas{position:relative;width:1200px;height:2350px;overflow:hidden}
  .abs{position:absolute}
  h1,h2,h3,.brand{font-family:"Montserrat",sans-serif}

  /* Hero */
  .hero{left:0;top:0;width:1200px;height:560px;background:radial-gradient(ellipse at 65% 45%,#1d3a5c 0%,#0d1f36 45%,var(--navy-deep) 100%)}
  .hero-scene{left:330px;top:70px;width:700px;height:460px;border-radius:50%;background:radial-gradient(ellipse at 55% 50%,rgba(120,150,185,.45) 0%,rgba(60,90,125,.25) 45%,rgba(13,31,54,0) 72%)}
  .hero-curve{left:0;top:440px}
  .hero-wordmark{left:45px;top:515px;transform:rotate(-90deg);transform-origin:0 0;font-family:"Didact Gothic",sans-serif;font-size:118px;letter-spacing:16px;color:rgba(95,199,173,.55)}
  .brand{left:211px;top:30px;display:flex;align-items:center;gap:14px;color:var(--white);font-weight:500;font-size:30px;letter-spacing:6px}
  .brand-dot{width:22px;height:22px;border:3px solid var(--teal);border-radius:50%}
  .nav{right:210px;top:44px;display:flex;gap:34px;list-style:none}
  .nav a{color:var(--white);font-family:"Montserrat",sans-serif;font-weight:600;font-size:10px;letter-spacing:.5px;text-decoration:none;text-transform:uppercase}
  .hero-title{left:211px;top:186px;color:var(--white);font-size:30px;font-weight:600;line-height:37px}
  .hero-sub{left:211px;top:276px;color:#dfe6ee;font-size:17px}
  .hero-links{left:211px;top:330px;display:flex;gap:22px}
  .hero-links a{color:var(--white);font-family:"Montserrat",sans-serif;font-size:10px;font-weight:700;text-decoration:none;padding-bottom:4px;border-bottom:2px solid var(--teal)}

  /* What we do */
  .about{left:0;top:520px;width:1200px;height:408px;background:var(--grey-bg)}
  .eyebrow{font-size:9px;color:var(--muted)}
  .eyebrow-rule{width:30px;height:2px;background:var(--ink)}
  .about-title{left:211px;top:660px;font-size:31px;font-weight:600;line-height:40px}
  .about-text{left:211px;top:753px;width:420px;font-size:11px;line-height:20px;color:#3a3d42}
  .pill{display:block;width:86px;height:32px;border-radius:16px;background:var(--teal);color:var(--white);font-family:"Montserrat",sans-serif;font-size:10px;font-weight:600;text-align:center;line-height:32px;text-decoration:none}
  .ghost-label{transform:rotate(-90deg);transform-origin:0 0;font-family:"Montserrat",sans-serif;font-weight:600;color:var(--ghost);white-space:nowrap}

  /* Services */
  .services-title{left:211px;top:1036px;font-size:30px;font-weight:600}
  .service{top:1102px;width:600px;height:376px;color:var(--white)}
  .service-digital{left:0;background:linear-gradient(135deg,#2a5a8c 0%,var(--blue-panel) 55%,#1a3a64 100%)}
  .service-call{left:600px;background:linear-gradient(135deg,#3b9583 0%,var(--green-panel) 55%,#1f6560 100%)}
  .service h3{position:absolute;top:56px;font-size:23px;font-weight:600}
  .service ul{position:absolute;top:100px;list-style:none;font-size:12px;line-height:17.4px}
  .outline-btn{position:absolute;display:block;width:90px;height:34px;border:1.5px solid var(--white);border-radius:17px;color:var(--white);font-family:"Montserrat",sans-serif;font-size:10px;font-weight:600;text-align:center;line-height:31px;text-decoration:none}

  /* FAQ */
  .faq{left:0;top:1478px;width:1200px;height:476px;background:var(--faq-bg)}
  .faq-title{left:0;top:1568px;width:1200px;text-align:center;font-size:24px;font-weight:600}
  .faq-rule{left:576px;top:1608px;width:48px;height:2px;background:#3a4a8a}
  .faq-sub{left:0;top:1628px;width:1200px;text-align:center;font-size:11px;color:#3a3d42}
  .faq-card{left:266px;top:1677px;width:668px;height:124px;background:var(--white);box-shadow:0 6px 16px rgba(20,40,70,.16)}
  .faq-answer{left:108px;top:30px;width:520px;font-size:11px;line-height:17px;color:#4a4e55}
  .faq-question{left:108px;top:88px;font-family:"Montserrat",sans-serif;font-size:10.5px;font-weight:600}
  .faq-brand{left:386px;top:80px;font-size:24px;letter-spacing:4px;color:#2c2f34;display:flex;align-items:center;gap:12px;font-family:"Didact Gothic",sans-serif}
  .faq-brand .brand-dot{border-color:var(--teal);width:26px;height:26px}
  .dots{left:570px;top:1872px;display:flex;gap:8px}
  .dots span{width:5px;height:5px;border-radius:50%;background:#222}
  .dots span.on{background:var(--teal)}

  /* Call back */
  .callback{left:0;top:1953px;width:1200px;height:304px;background:var(--teal-soft)}
  .callback-art{left:930px;top:1960px;width:250px;height:240px;background:radial-gradient(circle at 60% 25%,#8ee3c8 0%,#7dd6bf 35%,rgba(108,202,181,0) 70%)}
  .ground{left:0;top:2207px;width:1200px;height:50px;background:linear-gradient(var(--teal-card) 0 14px,#5dbfa8 14px 26px,#7fd4be 26px)}
  .contact-card{left:232px;top:2008px;width:245px;height:209px;background:var(--teal-card);color:var(--white);padding:24px 22px}
  .contact-card h3{font-size:12px;font-weight:600;margin-bottom:8px}
  .contact-card .rule{width:30px;height:2px;background:var(--white);margin-bottom:22px}
  .contact-row{display:flex;gap:10px;font-size:10px;line-height:14px;margin-bottom:12px}
  .contact-row svg{flex:none;margin-top:1px}
  .form-title{left:500px;top:2008px;color:var(--white);font-size:23px;font-weight:600}
  .field{width:225px;height:34px;border:1.5px solid var(--white);color:var(--white);font-size:10px;padding:0 12px;line-height:31px}
  .submit{left:500px;top:2171px;width:93px;height:35px;border:1.5px solid var(--white);border-radius:4px;color:var(--white);font-family:"Montserrat",sans-serif;font-size:10px;font-weight:600;text-align:center;line-height:32px}

  /* Footer */
  .copyright{left:211px;top:2288px;font-size:10px;line-height:17px;color:var(--muted)}
  .footer-nav{left:432px;top:2298px;display:flex;gap:28px;list-style:none}
  .footer-nav a{font-size:11px;color:var(--muted);text-decoration:none}
  .footer-nav a.current{color:var(--teal)}
  .social{left:884px;top:2294px;display:flex;gap:4px}
  .social span{width:23px;height:23px}
</style>
</head>
<body>
<div class="canvas">

  <!-- Hero -->
  <header class="abs hero"></header>
  <div class="abs hero-scene" role="img" aria-label="Illustration of a toy astronaut holding a flag beside a rocket on the moon under a starry sky"></div>
  <div class="abs hero-wordmark">LUNARO</div>
  <svg class="abs hero-curve" width="1200" height="120" viewBox="0 0 1200 120" aria-hidden="true">
    <path d="M0 80 Q600 -10 1200 80 L1200 120 L0 120 Z" fill="var(--grey-bg)"/>
  </svg>
  <div class="abs brand"><span class="brand-dot"></span>LUNARO</div>
  <ul class="abs nav">
    <li><a href="#">Home</a></li><li><a href="#">About Us</a></li><li><a href="#">Services</a></li>
    <li><a href="#">Pricing</a></li><li><a href="#">Contact Us</a></li><li><a href="#">Account</a></li>
  </ul>
  <h1 class="abs hero-title">Lunaro Is An<br>Omnichannel</h1>
  <p class="abs hero-sub">Provider For Customer Care</p>
  <div class="abs hero-links"><a href="#">LEARN MORE</a><a href="#">GET STARTED</a></div>

  <!-- What we do -->
  <section class="abs about"></section>
  <p class="abs eyebrow" style="left:211px;top:622px">What We Do</p>
  <div class="abs eyebrow-rule" style="left:211px;top:645px"></div>
  <h2 class="abs about-title">Lunaro is your personal customer<br>service and product research team.</h2>
  <p class="abs about-text">We love eCommerce, but we love seeing business owners succeed even more!<br>That is exactly why we have developed the processes and technology to take care of<br>the most over looked areas in eCommerce – Customer Service and Retention.</p>
  <a class="abs pill" href="#" style="left:211px;top:834px">More</a>
  <div class="abs ghost-label" style="left:1033px;top:836px;font-size:30px">What We Do</div>

  <!-- Services -->
  <p class="abs eyebrow" style="left:211px;top:998px">Our Services</p>
  <div class="abs eyebrow-rule" style="left:211px;top:1022px"></div>
  <h2 class="abs services-title">Lunaro Services</h2>

  <article class="abs service service-digital" role="img" aria-label="Photo of a person touching a digital network interface, tinted blue">
    <h3 style="left:211px">Digital Services</h3>
    <ul style="left:212px">
      <li>Email Support</li><li>Live Chat Support</li><li>Product Research</li>
      <li>Product Listing</li><li>Price Monitoring</li><li>Product Photo &amp; Video Editing</li>
    </ul>
    <a class="outline-btn" href="#" style="left:209px;top:248px">More</a>
  </article>
  <article class="abs service service-call" role="img" aria-label="Photo of a call center agent with a headset at a desk, tinted green">
    <h3 style="left:53px">Call Center Services</h3>
    <ul style="left:54px">
      <li>Answering service</li><li>Customer Upselling</li><li>Over-The-Phone Order Taking</li>
      <li>Order Return Processing</li><li>Feedback/Survey Calls</li><li>Message Delivering Service</li>
      <li>ROI Diagnostics &amp; Reporting</li><li>Scalable Call Center Pricing</li>
      <li>Customizable For Any Industry</li><li>100% US-Based Agents</li>
    </ul>
    <a class="outline-btn" href="#" style="left:53px;top:300px">More</a>
  </article>

  <!-- FAQ -->
  <section class="abs faq"></section>
  <h2 class="abs faq-title">Frequently Asked Quetions</h2>
  <div class="abs faq-rule"></div>
  <p class="abs faq-sub">Lorem Ipsum Dolor Sit Amet Consectetor Lorem Ipsum Dolor Sit Amet Consectetor</p>
  <div class="abs ghost-label" style="left:1040px;top:1908px;font-size:28px">Frequently Ask Question</div>
  <svg class="abs" style="left:268px;top:1684px" width="84" height="60" viewBox="0 0 84 60" aria-hidden="true">
    <path d="M6 60 V30 Q6 8 30 4 V16 Q20 20 20 30 H30 V60 Z M48 60 V30 Q48 8 72 4 V16 Q62 20 62 30 H72 V60 Z" fill="#eceff2"/>
  </svg>
  <div class="abs faq-card">
    <p class="abs faq-answer">The free trial only relates to the "call center" service packages! There is no hidden fine print or fees to get started. We don't even require any payment info, signatures, or deposits. If you don't like us or our service, just simply walk away.</p>
    <p class="abs faq-question">Is the free trial really free?</p>
    <div class="abs faq-brand"><span class="brand-dot"></span>LUNARO</div>
  </div>
  <svg class="abs" style="left:272px;top:1866px" width="20" height="12" viewBox="0 0 20 12" aria-label="Previous"><path d="M19 6H2M7 1L2 6l5 5" stroke="#777" stroke-width="1.6" fill="none"/></svg>
  <svg class="abs" style="left:907px;top:1866px" width="20" height="12" viewBox="0 0 20 12" aria-label="Next"><path d="M1 6h17M13 1l5 5-5 5" stroke="#777" stroke-width="1.6" fill="none"/></svg>
  <div class="abs dots"><span class="on"></span><span></span><span></span><span></span><span></span></div>

  <!-- Request call back -->
  <section class="abs callback"></section>
  <div class="abs callback-art" role="img" aria-label="Illustration of a moon, small astronauts and a rocket on a starry teal landscape"></div>
  <div class="abs ground"></div>
  <div class="abs contact-card">
    <h3>Contact Details</h3>
    <div class="rule"></div>
    <div class="contact-row">
      <svg width="11" height="11" viewBox="0 0 24 24" aria-hidden="true"><path d="M6.6 10.8a15 15 0 006.6 6.6l2.2-2.2c.3-.3.7-.4 1-.2 1.1.4 2.3.6 3.6.6.6 0 1 .4 1 1V20c0 .6-.4 1-1 1A17 17 0 013 4c0-.6.4-1 1-1h3.5c.6 0 1 .4 1 1 0 1.3.2 2.5.6 3.6.1.3 0 .7-.2 1z" fill="#fff"/></svg>
      <span>Phone: (800) 555-0147</span>
    </div>
    <div class="contact-row">
      <svg width="11" height="11" viewBox="0 0 24 24" aria-hidden="true"><rect x="2" y="5" width="20" height="14" fill="#fff"/><path d="M2 5l10 8 10-8" stroke="#84dac4" stroke-width="2" fill="none"/></svg>
      <span>hello@lunaro.inc</span>
    </div>
    <div class="contact-row">
      <svg width="11" height="12" viewBox="0 0 24 26" aria-hidden="true"><path d="M12 1a8 8 0 018 8c0 6-8 16-8 16S4 15 4 9a8 8 0 018-8z" fill="#fff"/><circle cx="12" cy="9" r="3" fill="#84dac4"/></svg>
      <span>Lunaro, Inc.<br>418 Corvan Ave. Delmont, CA 90210</span>
    </div>
  </div>
  <h2 class="abs form-title">Request For Call Back</h2>
  <div class="abs field" style="left:500px;top:2072px">Name</div>
  <div class="abs field" style="left:741px;top:2072px">Email</div>
  <div class="abs field" style="left:500px;top:2119px">Ph Num</div>
  <div class="abs field" style="left:741px;top:2119px">Enquiry About</div>
  <div class="abs submit">Submit Now</div>

  <!-- Footer -->
  <p class="abs copyright">Copyright © 2018<br>All rights reserved.</p>
  <ul class="abs footer-nav">
    <li><a class="current" href="#">Home</a></li><li><a href="#">About Us</a></li><li><a href="#">Service</a></li>
    <li><a href="#">Pricing</a></li><li><a href="#">Contact Us</a></li><li><a href="#">Account</a></li>
  </ul>
  <div class="abs social" aria-label="Social links">
    <span style="background:#2aa3dc"></span><span style="background:#3b5a98"></span>
    <span style="background:#3f729b"></span><span style="background:#d9473a"></span>
  </div>

</div>
</body>
</html>
```